Marlow Vale Stud website

We would like to create a horse stud/agistment farm website similar to this websites we have attached below:
www.thornbeck.com.au
www.quillstead.com.au
www.brackley.com
www.pimsey.com.au
The main colour scheme are purple and white to align with the stable's racing colours.
We have also attach the company logo and also images of the farm and create some ideas for the website.
Many thanks for looking into this project!

```html
<!DOCTYPE html>
<html lang="en">
<head>
<meta charset="utf-8">
<title>Marlow Vale Stud – Horse Farm</title>
<link href="https://fonts.googleapis.com/css2?family=Mulish:wght@400;600;700;800&display=swap" rel="stylesheet">
<style>
:root{
  --purple:#4b1b47;
  --purple-deep:#3a1237;
  --ink:#151515;
  --text:#555;
  --white:#fff;
  --footer:#1b1b1b;
  --footer-bar:#111;
  --muted:#cfcfcf;
}
*{margin:0;padding:0;box-sizing:border-box}
html,body{width:1200px;height:4245px;overflow:hidden}
body{position:relative;background:var(--white);font-family:'Mulish',sans-serif;color:var(--ink)}
.abs{position:absolute}

/* hero */
.hero{left:0;top:0;width:1200px;height:610px;background:linear-gradient(180deg,#2f62a8 0%,#6d9bd0 30%,#b7cbe0 48%,#3b5a2c 60%,#5e8a34 80%,#7aa03f 100%)}
.hero-edge{left:0;top:540px;width:1200px;height:72px}
.nav{top:76px;font-size:16px;font-weight:700;color:var(--white);letter-spacing:.3px;display:flex;gap:28px}
.nav-left{left:160px}
.nav-right{left:740px}
.brand-top{left:500px;top:92px;width:200px;text-align:center;color:var(--white);font-weight:800;font-size:20px}
.brand-top-dot{left:586px;top:24px;width:28px;height:28px;border:3px solid var(--white);border-radius:50%}
.phone{left:836px;top:16px;display:flex;align-items:center;gap:10px;color:var(--white);font-weight:800;font-size:20px}
.phone-ico{width:38px;height:38px;border-radius:50%;background:var(--purple);display:flex;align-items:center;justify-content:center}
.badge{left:432px;top:196px;width:336px;height:212px}
.badge-name{left:432px;top:316px;width:336px;text-align:center;color:var(--white);font-weight:800;font-size:28px}
.badge-sub{left:432px;top:358px;width:336px;text-align:center;color:var(--white);font-size:18px}
.explore{left:526px;top:438px;width:148px;height:44px;background:var(--purple);border:2px solid var(--white);outline:3px solid var(--purple);color:var(--white);font-weight:800;font-size:15px;display:flex;align-items:center;justify-content:center;letter-spacing:.5px}
.dots{left:1130px;top:276px;display:flex;flex-direction:column;align-items:center;gap:12px}
.dot{width:10px;height:10px;border-radius:50%;background:var(--white)}
.dot.active{width:20px;height:20px;border:3px solid var(--white);background:transparent;position:relative}
.dot.active::after{content:"";position:absolute;left:3px;top:3px;width:8px;height:8px;border-radius:50%;background:var(--white)}

/* headings */
.section-title{left:0;width:1200px;text-align:center;font-size:40px;font-weight:800;color:var(--ink)}

/* riding */
.riding-item{width:300px;text-align:center}
.riding-photo{width:206px;height:206px;border-radius:50%;margin:0 auto}
.riding-title{margin-top:36px;font-size:21px;font-weight:800;color:var(--purple)}
.riding-text{margin:12px auto 0;width:250px;font-size:16px;line-height:26px;color:var(--text)}

/* quote */
.quote-panel{left:113px;top:1234px;width:974px;height:600px;background:linear-gradient(180deg,#34558a 0%,#6f8fb8 35%,#3b3f3a 60%,#3d6a2a 85%,#557e32 100%)}
.quote{left:300px;top:1460px;width:600px;text-align:center;color:var(--white);font-size:28px;font-weight:700;line-height:41px}
.quote-author{left:300px;top:1606px;width:600px;text-align:center;color:var(--white);font-size:20px;font-weight:800}

/* farmers */
.farmer{width:218px;text-align:center}
.farmer-photo{width:218px;height:241px}
.farmer-name{margin-top:27px;font-size:21px;font-weight:800}
.farmer-role{margin-top:6px;font-size:15px;color:var(--text)}

/* gallery */
.tile{position:absolute}
.tile-more{background:var(--purple);display:flex;align-items:center;justify-content:center}

/* news */
.news{width:303px}
.news-photo{width:303px;height:190px}
.news-head{margin-top:26px;display:flex;gap:10px;align-items:center}
.date{flex:none;width:50px;height:50px;border-radius:50%;background:var(--purple);color:var(--white);text-align:center;font-weight:800;font-size:17px;line-height:18px;padding-top:8px}
.date small{display:block;font-size:10px;font-weight:600}
.news-title{font-size:17px;font-weight:800;line-height:23px}
.news-text{margin-top:14px;font-size:15px;line-height:23px;color:var(--text)}
.read{margin-top:18px;margin-left:4px;width:146px;height:44px;background:var(--purple);border:2px solid var(--white);outline:3px solid var(--purple);color:var(--white);font-weight:800;font-size:15px;display:flex;align-items:center;justify-content:center}

/* footer */
.footer{left:0;top:3800px;width:1200px;height:365px;background:var(--footer)}
.footer-edge{left:0;top:3770px;width:1200px;height:40px}
.footer-mark{left:183px;top:3900px;width:86px;height:86px;border:5px solid var(--white);border-radius:50%}
.footer-brand{left:96px;top:4030px;width:260px;text-align:center;color:var(--white);font-weight:800;font-size:24px}
.footer-head{top:3862px;color:var(--white);font-weight:800;font-size:21px}
.quick-links{left:418px;top:3910px;list-style:none;color:var(--white);font-size:15px;line-height:31px}
.fnews{left:586px;display:flex;gap:12px;width:200px}
.fnews-thumb{flex:none;width:72px;height:50px;background:linear-gradient(180deg,#9fb8cf,#5f8a3a)}
.fnews-text{color:var(--white);font-size:13px;line-height:16px}
.map{left:838px;top:3917px;width:249px;height:141px;background:linear-gradient(135deg,#eef0ea,#dfe6d8)}
.map-pin{left:926px;top:3956px;width:40px;height:40px;border-radius:50%;background:var(--purple);border:4px solid var(--white)}
.footer-bar{left:0;top:4162px;width:1200px;height:83px;background:var(--footer-bar)}
.copy{left:116px;top:4194px;color:var(--white);font-size:15px}
.social{top:4195px;width:20px;height:20px;border-radius:50%;background:var(--white)}
</style>
</head>
<body>

<header>
  <div class="abs hero" role="img" aria-label="Wide photo of green horse paddocks with fences under a blue sky"></div>
  <svg class="abs hero-edge" viewBox="0 0 1200 72" preserveAspectRatio="none" aria-hidden="true">
    <path fill="#fff" d="M0 36 L30 30 L55 44 L80 26 L110 40 L140 28 L170 46 L200 30 L235 42 L260 24 L295 40 L330 32 L360 50 L390 30 L420 44 L450 28 L480 42 L515 26 L545 46 L575 32 L610 44 L640 24 L670 40 L700 30 L735 48 L765 28 L795 42 L825 26 L860 44 L890 30 L920 46 L950 28 L985 40 L1015 24 L1045 42 L1075 30 L1105 46 L1135 28 L1165 40 L1200 30 L1200 72 L0 72 Z"/>
  </svg>

  <nav class="abs nav nav-left"><span>HOME</span><span>ABOUT US</span><span>STALLIONS</span></nav>
  <div class="abs brand-top-dot"></div>
  <div class="abs brand-top">Marlow Vale Stud</div>
  <nav class="abs nav nav-right"><span>FARM</span><span>PORTFOLIO</span><span>CONTACT US</span></nav>

  <div class="abs phone">
    <span class="phone-ico"><svg width="18" height="18" viewBox="0 0 24 24"><path fill="#fff" d="M6.6 10.8c1.4 2.8 3.8 5.1 6.6 6.6l2.2-2.2c.3-.3.7-.4 1-.2 1.1.4 2.3.6 3.6.6.6 0 1 .4 1 1V20c0 .6-.4 1-1 1C10.6 21 3 13.4 3 4c0-.6.4-1 1-1h3.5c.6 0 1 .4 1 1 0 1.3.2 2.5.6 3.6.1.3 0 .7-.2 1L6.6 10.8z"/></svg></span>
    (987) 555-0142
  </div>

  <svg class="abs badge" viewBox="0 0 336 212" aria-hidden="true">
    <path d="M2 82 H48 V52 H108 Q130 2 168 2 Q206 2 228 52 H288 V82 H334 V210 H2 Z" fill="#4b1b47" stroke="#fff" stroke-width="3"/>
    <path d="M10 90 H56 V60 H114 Q134 12 168 12 Q202 12 222 60 H280 V90 H326 V202 H10 Z" fill="none" stroke="#fff" stroke-width="1.5"/>
    <circle cx="168" cy="62" r="28" fill="none" stroke="#fff" stroke-width="4"/>
    <line x1="96" y1="160" x2="130" y2="160" stroke="#fff" stroke-width="1.5"/>
    <line x1="206" y1="160" x2="240" y2="160" stroke="#fff" stroke-width="1.5"/>
  </svg>
  <div class="abs badge-name">Marlow Vale Stud</div>
  <div class="abs badge-sub">Horse Farm</div>
  <div class="abs explore">EXPLORE</div>

  <div class="abs dots"><span class="dot active"></span><span class="dot"></span><span class="dot"></span></div>
</header>

<section>
  <h2 class="abs section-title" style="top:672px">Enjoy the Horseback Riding</h2>
  <div class="abs riding-item" style="left:142px;top:796px">
    <div class="riding-photo" role="img" aria-label="Racehorse and jockey in purple silks on the track" style="background:radial-gradient(circle,#c9b9a0,#6f7a4d)"></div>
    <h3 class="riding-title">Joy Riding</h3>
    <p class="riding-text">Nam libero tempore, cum soluta nobis est eligendi optio cumque nihil impedit quo</p>
  </div>
  <div class="abs riding-item" style="left:450px;top:796px">
    <div class="riding-photo" role="img" aria-label="Group of dark horses standing in a field under a blue sky" style="background:linear-gradient(180deg,#6f9ad4,#3b3a33 60%,#6b8f3a)"></div>
    <h3 class="riding-title">Group Riding</h3>
    <p class="riding-text">Nam libero tempore, cum soluta nobis est eligendi optio cumque nihil impedit quo</p>
  </div>
  <div class="abs riding-item" style="left:764px;top:796px">
    <div class="riding-photo" role="img" aria-label="Aerial view of the horse farm buildings and paddocks" style="background:radial-gradient(circle,#b9b49a,#5d8a3c)"></div>
    <h3 class="riding-title">Horse Farm</h3>
    <p class="riding-text">Nam libero tempore, cum soluta nobis est eligendi optio cumque nihil impedit quo</p>
  </div>
</section>

<section>
  <div class="abs quote-panel" role="img" aria-label="Herd of dark horses standing in a grass paddock under cloudy sky"></div>
  <blockquote class="abs quote">“A horse is a thing of beauty... none will tire of looking at him as long as he displays himself in his splendor.”</blockquote>
  <div class="abs quote-author">- John Smith</div>
</section>

<section>
  <h2 class="abs section-title" style="top:1932px">Meet The Farmers</h2>
  <div class="abs farmer" style="left:127px;top:2026px">
    <div class="farmer-photo" role="img" aria-label="Farmer on horseback in a wheat field" style="background:linear-gradient(180deg,#8fb5dc,#c9b27a)"></div>
    <h3 class="farmer-name">Derreck Dondarion</h3><p class="farmer-role">Master of haystack</p>
  </div>
  <div class="abs farmer" style="left:370px;top:2026px">
    <div class="farmer-photo" role="img" aria-label="Farmer patting a horse in a stable" style="background:linear-gradient(135deg,#8a5a3a,#3d2a20)"></div>
    <h3 class="farmer-name">Carlos Martell</h3><p class="farmer-role">spanish mustang</p>
  </div>
  <div class="abs farmer" style="left:611px;top:2026px">
    <div class="farmer-photo" role="img" aria-label="Farmer with a brown horse in the barn" style="background:linear-gradient(135deg,#6b4a33,#a9825c)"></div>
    <h3 class="farmer-name">Gandor Ged Clegane</h3><p class="farmer-role">arabian horse</p>
  </div>
  <div class="abs farmer" style="left:855px;top:2026px">
    <div class="farmer-photo" role="img" aria-label="Farmer hugging a grey horse" style="background:linear-gradient(135deg,#9aa39a,#c98c5c)"></div>
    <h3 class="farmer-name">John Doe</h3><p class="farmer-role">the local mascot</p>
  </div>
</section>

<section class="gallery">
  <div class="tile" style="left:0;top:2462px;width:597px;height:294px;background:linear-gradient(180deg,#a9c2d6,#5e8d3c 40%,#7aa04a)" role="img" aria-label="Aerial view of stud farm and paddocks"></div>
  <div class="tile" style="left:606px;top:2462px;width:291px;height:294px;background:linear-gradient(180deg,#5f8fd0,#3a3a32 60%,#6e9a3a)" role="img" aria-label="Horses standing together under blue sky"></div>
  <div class="tile" style="left:906px;top:2462px;width:294px;height:294px;background:linear-gradient(180deg,#8fb1cf,#5a8c3a 40%,#86a94c)" role="img" aria-label="Fenced paddocks with stables"></div>
  <div class="tile" style="left:0;top:2768px;width:292px;height:294px;background:linear-gradient(135deg,#d7b58a,#9b5d3a 60%,#6a2a2a)" role="img" aria-label="Rider in a cowboy hat beside a chestnut horse"></div>
  <div class="tile tile-more" style="left:303px;top:2768px;width:291px;height:294px">
    <svg width="56" height="56" viewBox="0 0 56 56" aria-label="View more"><circle cx="28" cy="28" r="25" fill="none" stroke="#fff" stroke-width="3"/><path d="M28 16v24M16 28h24" stroke="#fff" stroke-width="3"/></svg>
  </div>
  <div class="tile" style="left:606px;top:2768px;width:594px;height:294px;background:linear-gradient(180deg,#d9cfa8,#7d9a5a 45%,#3f6a2a)" role="img" aria-label="Horses grazing in a sunlit field at sunset"></div>
</section>

<section>
  <h2 class="abs section-title" style="top:3160px">Our News</h2>
  <article class="abs news" style="left:110px;top:3263px">
    <div class="news-photo" role="img" aria-label="Horses grazing by a white fence" style="background:linear-gradient(180deg,#a7c3de,#5d8a3a 50%,#6c9640)"></div>
    <div class="news-head"><span class="date">29<small>Feb</small></span><h3 class="news-title">At vero eos et accusamus et iusto odio dignissimos</h3></div>
    <p class="news-text">Lorem ipsum dolor sit amet, consectetur adipiscing elit, sed do eiusmod tempor incididunt ut labore et dolore magna</p>
    <div class="read">Read More</div>
  </article>
  <article class="abs news" style="left:444px;top:3263px">
    <div class="news-photo" role="img" aria-label="Farmer feeding hay to a white horse" style="background:linear-gradient(135deg,#d9d2c2,#9c8462)"></div>
    <div class="news-head"><span class="date">29<small>Feb</small></span><h3 class="news-title">At vero eos et accusamus et iusto odio dignissimos</h3></div>
    <p class="news-text">Lorem ipsum dolor sit amet, consectetur adipiscing elit, sed do eiusmod tempor incididunt ut labore et dolore magna</p>
    <div class="read">Read More</div>
  </article>
  <article class="abs news" style="left:781px;top:3263px">
    <div class="news-photo" role="img" aria-label="Mare and foal in a green paddock" style="background:linear-gradient(180deg,#e0c9a8,#6b8d44 50%,#577a34)"></div>
    <div class="news-head"><span class="date">29<small>Feb</small></span><h3 class="news-title">At vero eos et accusamus et iusto odio dignissimos</h3></div>
    <p class="news-text">Lorem ipsum dolor sit amet, consectetur adipiscing elit, sed do eiusmod tempor incididunt ut labore et dolore magna</p>
    <div class="read">Read More</div>
  </article>
</section>

<footer>
  <svg class="abs footer-edge" viewBox="0 0 1200 40" preserveAspectRatio="none" aria-hidden="true">
    <path fill="#1b1b1b" d="M0 18 L28 10 L55 24 L85 8 L115 22 L145 12 L175 28 L205 10 L240 24 L270 6 L300 20 L335 12 L365 28 L395 10 L425 22 L455 8 L490 24 L520 12 L550 28 L580 10 L615 22 L645 6 L675 20 L705 12 L740 28 L770 10 L800 24 L830 8 L865 22 L895 12 L925 28 L955 10 L990 22 L1020 6 L1050 24 L1080 12 L1110 26 L1140 8 L1170 22 L1200 12 L1200 40 L0 40 Z"/>
  </svg>
  <div class="abs footer"></div>
  <div class="abs footer-mark"></div>
  <div class="abs footer-brand">Marlow Vale Stud</div>

  <h4 class="abs footer-head" style="left:416px">Quick Links</h4>
  <ul class="abs quick-links"><li>Home</li><li>About Us</li><li>Stallions</li><li>Farm</li><li>Portfolio</li><li>Contact Us</li></ul>

  <h4 class="abs footer-head" style="left:586px">Latest News</h4>
  <div class="abs fnews" style="top:3918px"><span class="fnews-thumb" role="img" aria-label="Farm news thumbnail"></span><span class="fnews-text">Nam libero tempore, cum soluta nobis est eligendi</span></div>
  <div class="abs fnews" style="top:3986px"><span class="fnews-thumb" role="img" aria-label="Farm news thumbnail"></span><span class="fnews-text">Nam libero tempore, cum soluta nobis est eligendi</span></div>
  <div class="abs fnews" style="top:4054px"><span class="fnews-thumb" role="img" aria-label="Farm news thumbnail"></span><span class="fnews-text">Nam libero tempore, cum soluta nobis est eligendi</span></div>

  <h4 class="abs footer-head" style="left:838px">Locations</h4>
  <div class="abs map" role="img" aria-label="Map showing the farm location"></div>
  <div class="abs map-pin"></div>

  <div class="abs footer-bar"></div>
  <p class="abs copy">© 2019 Copyrights | All Rights Reserved</p>
  <span class="abs social" style="left:978px" aria-label="Social link"></span>
  <span class="abs social" style="left:1020px" aria-label="Social link"></span>
  <span class="abs social" style="left:1063px" aria-label="Social link"></span>
</footer>

</body>
</html>
```